Web design required

1-We need a web design for existing company based in New Zealand
2-We build residential house and light commercial
3-We has in-house designer which allow us can provide interior design
4-We modeling project before site construction, which enable both client and construction team to visually analysis whole project,

Target Market(s)

middle class residential house market
Ref: http://www.parvellbuilders.co.nz/

Industry/Entity Type

Construction Company

Number of Pages Required

1 page

Font styles to use
Sans Serif
Other font styles liked:
• Such as : Central Gothic or similar which has more design taste

Colors

Designer to choose colors to be used in the design.

Requirements
Must have
• Front sheet, contact information, sample project

```html
<!DOCTYPE html>
<html lang="en">
<head>
<meta charset="utf-8">
<title>Harbourline Homes</title>
<link href="https://fonts.googleapis.com/css2?family=Questrial&family=Open+Sans:wght@400;600&display=swap" rel="stylesheet">
<style>
:root{
  --blue:#1f4fa8;
  --blue-deep:#173c86;
  --navy:#0e2148;
  --ink:#1d2230;
  --dark:#17191e;
  --grey:#6b7280;
  --white:#ffffff;
}
*{box-sizing:border-box;margin:0;padding:0}
html,body{width:1200px;height:2784px;overflow:hidden;background:var(--white)}
body{position:relative;font-family:"Open Sans",Arial,sans-serif;color:var(--ink)}
.heading{font-family:"Questrial","Century Gothic",sans-serif;font-weight:400}
section{position:absolute;left:0;width:1200px;overflow:hidden}
.fill{position:absolute}

/* hero */
.hero{top:0;height:620px}
.hero-photo{inset:0;background:linear-gradient(180deg,#8fa3b8 0%,#c9d2da 35%,#b9bfc2 55%,#4f6b3a 75%,#2f4724 100%)}
.hero-shade{inset:0;background:linear-gradient(180deg,rgba(14,33,72,.15),rgba(14,33,72,.35))}
.brand{position:absolute;left:0;top:0;width:440px;height:88px;background:var(--white);display:flex;align-items:center;gap:12px;padding-left:30px;clip-path:polygon(0 0,100% 0,88% 100%,0 100%)}
.brand-mark{width:30px;height:30px;background:var(--blue);flex:none}
.brand-name{font-family:"Questrial",sans-serif;font-size:23px;color:var(--navy);letter-spacing:.5px;white-space:nowrap}
.nav{position:absolute;right:0;top:0;width:720px;height:88px;background:var(--blue-deep);clip-path:polygon(6% 0,100% 0,100% 100%,0 100%);display:flex;justify-content:flex-end;align-items:center;gap:40px;padding-right:100px}
.nav a{color:var(--white);text-decoration:none;font-size:17px}
.hero-title{position:absolute;top:345px;width:100%;text-align:center;color:var(--white);font-size:38px;text-shadow:0 2px 8px rgba(0,0,0,.4)}

/* services */
.services{top:620px;height:580px;background:var(--white)}
.services-panel{left:0;top:0;width:620px;height:580px}
.services-title{position:absolute;left:150px;top:175px;color:var(--white);font-size:66px;line-height:1.15}
.service{position:absolute;left:540px;width:600px;display:flex;gap:34px}
.service-icon{width:86px;height:86px;flex:none;border:3px solid var(--blue);background:var(--white);display:flex;align-items:center;justify-content:center}
.service h3{font-family:"Questrial",sans-serif;font-size:24px;color:var(--blue-deep);margin:8px 0 12px}
.service p{font-size:13.5px;line-height:1.65;color:var(--grey);max-width:470px}

/* about */
.about{top:1200px;height:420px}
.about-photo{inset:0;background:linear-gradient(180deg,#e9edf2,#f7f8fa 60%,#dfe4ea)}
.about-title{position:absolute;top:78px;width:100%;text-align:center;color:var(--blue-deep);font-size:58px}
.about-text{position:absolute;top:180px;left:270px;width:660px;text-align:center;font-size:15px;line-height:1.8;color:#4b5563}
.about-text p+p{margin-top:16px}

/* projects */
.projects{top:1620px;height:600px;background:var(--navy)}
.projects-blue{left:540px;top:0;width:660px;height:600px;background:linear-gradient(135deg,#2a5cbc,#1a418f)}
.tile{position:absolute;overflow:hidden}
.tile .fill{inset:0}
.tile-label{position:absolute;color:var(--white);font-family:"Questrial",sans-serif;font-size:30px;text-shadow:0 2px 6px rgba(0,0,0,.6);line-height:1.15;white-space:nowrap}
.projects-title{position:absolute;left:820px;top:220px;color:var(--white);font-size:66px;line-height:1.15}

/* contact */
.contact{top:2220px;height:564px;background:var(--dark)}
.contact-photo{inset:0;background:linear-gradient(180deg,#23262d,#121317)}
.contact-title{position:absolute;top:34px;width:100%;text-align:center;color:var(--white);font-size:56px}
.col{position:absolute;top:150px;color:var(--white)}
.col h4{font-size:20px;font-weight:600;margin-bottom:14px}
.col p{font-size:12.5px;line-height:1.7;color:#c9ccd3}
.inquiries{left:100px;width:260px}
.field{width:240px;height:30px;border:1px solid #5b5f69;margin-top:12px;padding:6px 10px;font-size:12px;color:#c9ccd3}
.field.tall{height:46px}
.send{margin-top:14px;width:120px;height:30px;background:var(--blue);color:var(--white);font-size:13px;display:flex;align-items:center;justify-content:center}
.office{left:500px;width:300px}
.office .block+.block{margin-top:34px}
.follow{left:890px;width:280px}
.socials{display:flex;gap:14px;margin-bottom:40px}
.socials span{width:34px;height:34px;border:1.5px solid var(--white);border-radius:50%}
.phone{font-size:26px;font-weight:600;color:var(--white);margin-bottom:40px}
.foot-brand{display:flex;align-items:center;gap:10px}
.foot-brand .brand-mark{width:26px;height:26px}
.foot-brand span{font-family:"Questrial",sans-serif;font-size:21px;color:var(--white);white-space:nowrap}
.footer{position:absolute;left:0;bottom:0;width:100%;height:46px;border-top:1px solid #33363e;display:flex;align-items:center;justify-content:center;font-size:12px;color:#9aa0aa}
</style>
</head>
<body>

<section class="hero">
  <div class="fill hero-photo" role="img" aria-label="Photograph of a modern two-storey family home with a grey roof and a green lawn"></div>
  <div class="fill hero-shade"></div>
  <div class="brand"><span class="brand-mark"></span><span class="brand-name">HARBOURLINE HOMES</span></div>
  <nav class="nav"><a href="#">Home</a><a href="#">Services</a><a href="#">About</a><a href="#">Projects</a><a href="#">Contact</a></nav>
  <h1 class="hero-title heading">Welcome To Harbourline Homes</h1>
</section>

<section class="services">
  <svg class="fill services-panel" viewBox="0 0 620 580" role="img" aria-label="Blue-tinted photograph of a house under construction">
    <defs><linearGradient id="svcGrad" x1="0" y1="0" x2="1" y2="1"><stop offset="0" stop-color="#2b5fc0"/><stop offset="1" stop-color="#14367c"/></linearGradient></defs>
    <polygon points="0,0 560,0 430,580 0,580" fill="url(#svcGrad)"/>
    <polygon points="560,0 620,0 470,580 430,580" fill="#1f4fa8" opacity=".35"/>
  </svg>
  <h2 class="services-title heading">Our<br>Services</h2>

  <div class="service" style="top:90px">
    <div class="service-icon"><svg width="48" height="48" viewBox="0 0 48 48" fill="none" stroke="#1f4fa8" stroke-width="2.5"><rect x="10" y="8" width="28" height="34"/><rect x="18" y="4" width="12" height="8"/><path d="M16 22h16M16 29h16M16 36h10"/></svg></div>
    <div><h3>Preconstruction Planning</h3><p>We review your site, budget and goals early, then set out a clear plan, timeline and cost estimate so every stage of the build runs smoothly.</p></div>
  </div>
  <div class="service" style="top:250px">
    <div class="service-icon"><svg width="48" height="48" viewBox="0 0 48 48" fill="none" stroke="#1f4fa8" stroke-width="2.5"><path d="M6 24 24 8l18 16"/><path d="M11 20v20h26V20"/><rect x="20" y="28" width="8" height="12"/></svg></div>
    <div><h3>Construction Modelling</h3><p>Every project is modelled before work starts on site, letting you and our team walk through the whole home and resolve details in advance.</p></div>
  </div>
  <div class="service" style="top:410px">
    <div class="service-icon"><svg width="48" height="48" viewBox="0 0 48 48" fill="none" stroke="#1f4fa8" stroke-width="2.5"><circle cx="24" cy="16" r="7"/><path d="M10 42c0-8 6-13 14-13s14 5 14 13"/></svg></div>
    <div><h3>Full Project Management</h3><p>One dedicated manager handles trades, consents and quality checks from first sketch to handover, keeping you informed at every step.</p></div>
  </div>
</section>

<section class="about">
  <div class="fill about-photo" role="img" aria-label="Faded photograph of a timber-framed house under construction"></div>
  <h2 class="about-title heading">About Us</h2>
  <div class="about-text">
    <p>Harbourline Homes is dedicated to creating and renovating beautiful and unique homes and buildings.</p>
    <p>Our team works with you to take dream homes off the drawing board and into reality. We have the knowledge and expertise to customise homes to suit you, from unusual materials and designs to environmentally sensitive locations.</p>
  </div>
</section>

<section class="projects">
  <div class="fill projects-blue" role="img" aria-label="Blue overlay on architectural plans of a house"></div>
  <div class="tile" style="left:0;top:0;width:540px;height:280px">
    <div class="fill" role="img" aria-label="Photograph of the Kowhai project, a new two-storey home" style="background:linear-gradient(160deg,#7d8b99,#3c4652 60%,#2a3038)"></div>
    <div class="tile-label" style="left:120px;top:215px">Kowhai Project &nbsp;›</div>
  </div>
  <div class="tile" style="left:0;top:280px;width:300px;height:320px">
    <div class="fill" role="img" aria-label="Photograph of the Ridgeview project interior with a timber staircase" style="background:linear-gradient(150deg,#8a6a4c,#4b3a2c 55%,#2b221b)"></div>
    <div class="tile-label" style="left:30px;top:185px">Ridgeview Project &nbsp;›<br>Interior</div>
  </div>
  <div class="tile" style="left:300px;top:280px;width:360px;height:320px;clip-path:polygon(0 0,82% 0,100% 100%,0 100%)">
    <div class="fill" role="img" aria-label="Photograph of the Elm Rd project, a modern home with a flat roof" style="background:linear-gradient(160deg,#9aa7b3,#4f5b66 55%,#2e363e)"></div>
    <div class="tile-label" style="left:50px;top:190px">Elm Rd Project &nbsp;›</div>
  </div>
  <h2 class="projects-title heading">Our<br>Projects</h2>
</section>

<section class="contact">
  <div class="fill contact-photo" role="img" aria-label="Dark photograph of a house at night"></div>
  <h2 class="contact-title heading">Contact</h2>

  <div class="col inquiries">
    <h4>Inquiries</h4>
    <p>For any inquiries, questions or commendations, please fill out the following form.</p>
    <div class="field">Name</div>
    <div class="field">Email</div>
    <div class="field">Subject</div>
    <div class="field tall">Message</div>
    <div class="send">Send</div>
  </div>

  <div class="col office">
    <div class="block">
      <h4>Head Office</h4>
      <p>12 Kestrel Lane, Auckland<br>info@harbourlinehomes.co.nz<br>Tel: 09 555 0142</p>
    </div>
    <div class="block">
      <h4>Employment</h4>
      <p>To apply for a job with Harbourline Homes, please send a cover letter together with your CV to info@harbourlinehomes.co.nz</p>
    </div>
  </div>

  <div class="col follow">
    <h4>Follow Us</h4>
    <div class="socials"><span></span><span></span><span></span><span></span></div>
    <h4>Get a quote</h4>
    <div class="phone">09 555 0142</div>
    <div class="foot-brand"><span class="brand-mark"></span><span>HARBOURLINE HOMES</span></div>
  </div>

  <div class="footer">© 2017 | www.harbourlinehomes.co.nz</div>
</section>

</body>
</html>
```